Business Card & Letterhead Design

We a financial advice company based in Australia. We provide advice to wealthy farmers.

We are changing our business name FROM Brightvale Financial TO Tallowmere Wealth and we need a new letterhead and double sided business card design

Attached is designs from our previous branding (Brightvale Financial) as it includes all the details we require on the new Tallowmere Wealth business cards and letterhead.

Need extra days to review

```html
<!DOCTYPE html>
<html lang="en">
<head>
<meta charset="utf-8">
<title>Tallowmere Wealth Letterhead</title>
<link rel="stylesheet" href="https://fonts.googleapis.com/css2?family=Open+Sans:wght@400;600;700&display=swap">
<style>
  :root {
    --paper: #ffffff;
    --ink: #2b2b2b;
    --body-ink: #555555;
    --rule: #2b2b2b;
    --watermark: #ececec;
  }
  * { margin: 0; padding: 0; box-sizing: border-box; }
  html, body { width: 1040px; height: 1200px; overflow: hidden; background: var(--paper); }
  .letterhead {
    position: relative; width: 1040px; height: 1200px;
    background: var(--paper); color: var(--ink);
    font-family: "Open Sans", Arial, sans-serif;
  }
  .brand { position: absolute; left: 98px; top: 26px; width: 280px; text-align: center; }
  .brand-mark { display: block; margin: 0 auto; }
  .brand-name {
    margin-top: 10px; font-family: "Open Sans", Arial, sans-serif; font-weight: 400;
    font-size: 23px; letter-spacing: 1.5px; text-transform: uppercase; color: var(--ink);
  }
  .sender {
    position: absolute; right: 98px; top: 44px; text-align: right; font-style: normal;
    font-size: 16px; line-height: 22.5px; color: var(--ink);
  }
  .sender .gap { margin-top: 4px; }
  .sender b { font-weight: 700; }
  .watermark { position: absolute; left: 342px; top: 490px; }
  .meta { position: absolute; left: 98px; font-size: 15px; line-height: 19px; color: var(--body-ink); }
  .date { top: 285px; }
  .recipient { top: 318px; }
  .salutation { top: 425px; }
  .body {
    position: absolute; left: 98px; width: 844px; top: 474px;
    font-size: 15.2px; line-height: 27px; color: var(--body-ink); text-align: justify;
  }
  .body p + p { margin-top: 27px; }
  .closing { position: absolute; left: 98px; top: 882px; font-size: 15px; color: var(--body-ink); }
  .signatory { position: absolute; left: 98px; top: 952px; }
  .signatory .name { font-size: 18.5px; font-weight: 600; color: var(--ink); }
  .signatory .role { font-size: 15px; color: var(--body-ink); margin-top: 4px; }
  .footer { position: absolute; left: 98px; width: 844px; top: 1082px; }
  .footer-tags {
    display: flex; justify-content: space-between; padding: 0 8px 0 4px;
    font-size: 14.5px; font-weight: 700; color: var(--ink);
  }
  .footer-rule { height: 3px; background: var(--rule); margin-top: 5px; }
  .footer-legal { text-align: center; font-size: 16px; line-height: 23px; margin-top: 10px; color: var(--ink); }
</style>
</head>
<body>
<main class="letterhead">
  <header>
    <div class="brand">
      <svg class="brand-mark" width="72" height="72" viewBox="0 0 72 72" aria-hidden="true">
        <circle cx="36" cy="36" r="33" fill="none" stroke="#2b2b2b" stroke-width="2.5"/>
      </svg>
      <div class="brand-name">Tallowmere Wealth</div>
    </div>
    <address class="sender">
      <div>Corvane Holdings Pty Ltd&nbsp; ATF The Ashdown</div>
      <div>Investment Trust T/AS Brightvale Financial</div>
      <div class="gap"><b>ABN:</b> 48 302 917 655</div>
      <div class="gap">Corporate Authorised Representative</div>
      <div>Of Meridale Financial Planning Limited</div>
      <div class="gap">Suite 4A, 18 Harwick St Riverside QLD 4170</div>
      <div>PO Box 5521 Eastvale QLD 4170</div>
      <div class="gap"><b>P:</b> (07) 3155 0142 | <b>F:</b> (07) 3155 0199</div>
      <div><b>E:</b> office@brightvalefinancial.com.au</div>
      <div><b>W:</b> www.brightvalefinancial.com.au</div>
    </address>
  </header>

  <svg class="watermark" width="356" height="356" viewBox="0 0 356 356" aria-hidden="true">
    <circle cx="178" cy="178" r="172" fill="none" stroke="var(--watermark)" stroke-width="6"/>
  </svg>

  <div class="meta date">Issuing Date: May 5, 2018</div>
  <div class="meta recipient">
    Name Of Employee Mr. XYZABC<br>Address of Employee<br>Address Line 2 etc..
  </div>
  <div class="meta salutation">Dear Mr.XYZABC</div>

  <section class="body">
    <p>Lorem Ipsum has been the industry's standard dummy text ever since the 1500s, when an unknown printer took a galley of type and scrambled it to make a type specimen book. It has survived not only five centuries, but also the leap into electronic typesetting, remaining essentially unchanged. It was popularised in the 1960s with the release of Presscraft sheets containing Lorem Ipsum passages, and more recently with desktop publishing software like Folio LayoutDesk including versions of Lorem Ipsum.</p>
    <p>Lorem Ipsum is simply dummy text of the printing and typesetting industry. Lorem Ipsum has been the industry's standard dummy text ever since the 1500s, when an unknown printer took a galley of type and scrambled it to make a type specimen book.</p>
    <p>It has survived not only five centuries, but also the leap into electronic typesetting, remaining essentially unchanged. It was popularised in the 1960s with the release of Presscraft sheets containing Lorem IpsumIpsum passages.</p>
  </section>

  <div class="closing">Yours Sincerely</div>
  <div class="signatory">
    <div class="name">Marcus Hale</div>
    <div class="role">Managing Director</div>
  </div>

  <footer class="footer">
    <div class="footer-tags"><span>‘FINANCIAL PEACE OF MIND’</span><span>A REFERRAL BUILT BUSINESS</span></div>
    <div class="footer-rule"></div>
    <div class="footer-legal">
      <div>Meridale Financial Planning Limited &nbsp;| ABN 61 004 283 517</div>
      <div>Australian &nbsp;Financial Services License | License Number 318472</div>
      <div>Principle Address: 410 Ardley St. PO Box 1946 Southport VIC 3009</div>
    </div>
  </footer>
</main>
</body>
</html>
```